New business card/stationary for a consulting company

I am looking for a clean and very professional looking business card for my consulting company as well as corresponding stationary. I am uploading our logo. I like simple and powerful for the feel. No graphics but I am open on everything else. Below is my contact information but would like the final to be in a version I can add my employees information into and print. Thank you.

Daniel Whitcombe
dan@ferncliffadvisory.com
2870 North 9th Avenue, Summit Floor, Elm Ridge, Illinois 60531
www.ferncliffadvisory.com

Industry/Entity Type

Consulting

Contact Information for Business Card

Daniel Whitcombe
dan@ferncliffadvisory.com
www.ferncliffadvisory.com

Font styles to use
Serif
Sans Serif

Requirements
Must have
• Our logo and the business card details.
Nice to have
• our website www.ferncliffadvisory.com

```html
<!DOCTYPE html>
<html lang="en">
<head>
<meta charset="utf-8">
<title>Ferncliff Advisory — Business Card</title>
<link rel="stylesheet" href="https://fonts.googleapis.com/css2?family=Montserrat:wght@400;600;700;800&display=swap">
<style>
  :root {
    --navy: #0a0a96;
    --navy-deep: #03034c;
    --white: #ffffff;
    --backdrop: #e9e9ea;
    --ink: #0d0d8a;
  }
  * { box-sizing: border-box; margin: 0; padding: 0; }
  html, body {
    width: 1200px; height: 900px; overflow: hidden;
    background: var(--backdrop);
    font-family: "Montserrat", sans-serif;
  }
  .card {
    position: absolute; left: 75px; top: 150px;
    width: 1050px; height: 600px;
    background: var(--white);
    overflow: hidden;
    box-shadow: 0 18px 40px rgba(0,0,0,0.18);
  }
  .card-band {
    position: absolute; left: 0; top: 0; width: 1050px; height: 600px;
  }
  .brand {
    position: absolute; left: 0; right: 0; top: 78px;
    display: flex; align-items: center; justify-content: center; gap: 22px;
  }
  .brand-square {
    width: 58px; height: 58px; background: var(--ink);
  }
  .brand-name {
    font-size: 46px; font-weight: 400; letter-spacing: 2px;
    color: var(--ink); text-transform: uppercase;
  }
  .person {
    position: absolute; left: 80px; top: 300px; color: var(--white);
  }
  .person-name { font-size: 40px; font-weight: 800; margin-bottom: 10px; }
  .person-title { font-size: 25px; font-weight: 700; margin-bottom: 14px; }
  .person-address { font-size: 23px; font-weight: 400; line-height: 1.45; }
  .divider {
    position: absolute; left: 590px; top: 330px; width: 2px; height: 190px;
    background: var(--white);
  }
  .contact {
    position: absolute; left: 625px; top: 334px; list-style: none; color: var(--white);
  }
  .contact li {
    display: flex; align-items: center; gap: 16px;
    font-size: 24px; font-weight: 400; height: 44px;
  }
  .contact svg { width: 22px; height: 22px; flex: none; }
</style>
</head>
<body>
  <div class="card">
    <svg class="card-band" viewBox="0 0 1050 600" aria-hidden="true">
      <defs>
        <linearGradient id="bandFill" x1="0" y1="0" x2="1" y2="1">
          <stop offset="0" stop-color="#0b0ba6"/>
          <stop offset="1" stop-color="#03034a"/>
        </linearGradient>
      </defs>
      <path d="M0 250 H70 L90 272 L110 250 H1050 V600 H0 Z" fill="url(#bandFill)"/>
    </svg>

    <div class="brand">
      <span class="brand-square"></span>
      <span class="brand-name">Ferncliff Advisory</span>
    </div>

    <div class="person">
      <p class="person-name">Daniel Whitcombe</p>
      <p class="person-title">Founder / Principal</p>
      <p class="person-address">2870 North 9th Avenue, Summit Floor,<br>Elm Ridge, Illinois 60531</p>
    </div>

    <div class="divider"></div>

    <ul class="contact">
      <li>
        <svg viewBox="0 0 24 24"><path fill="#fff" d="M6.6 10.8a15 15 0 0 0 6.6 6.6l2.2-2.2c.3-.3.7-.4 1-.2 1.1.4 2.3.6 3.6.6.6 0 1 .4 1 1V20c0 .6-.4 1-1 1A17 17 0 0 1 3 4c0-.6.4-1 1-1h3.5c.6 0 1 .4 1 1 0 1.3.2 2.5.6 3.6.1.3 0 .7-.2 1z"/></svg>
        (855) 372 40816
      </li>
      <li>
        <svg viewBox="0 0 24 24"><rect x="6" y="2" width="12" height="20" rx="2" fill="none" stroke="#fff" stroke-width="2"/><circle cx="12" cy="18" r="1.2" fill="#fff"/></svg>
        + 917362048195
      </li>
      <li>
        <svg viewBox="0 0 24 24"><rect x="2" y="5" width="20" height="14" rx="1.5" fill="#fff"/><path d="M3 6l9 7 9-7" fill="none" stroke="#03034c" stroke-width="1.6"/></svg>
        dan@ferncliffadvisory.com
      </li>
      <li>
        <svg viewBox="0 0 24 24" fill="none" stroke="#fff" stroke-width="1.6"><circle cx="12" cy="12" r="9.5"/><ellipse cx="12" cy="12" rx="4" ry="9.5"/><path d="M2.5 12h19M4 7h16M4 17h16"/></svg>
        www.ferncliffadvisory.com
      </li>
    </ul>
  </div>
</body>
</html>
```